Business card design for my company.
I would like the card's background colour to be black. You can also see our web site to get an idea of our brand. https://www.tmwhomecrafting.com.au/
- Name
- Email

```html
<!DOCTYPE html>
<html lang="en">
<head>
<meta charset="utf-8">
<title>TMW Home Crafting – Business Card</title>
<link rel="stylesheet" href="https://fonts.googleapis.com/css2?family=Montserrat:wght@400;500;700;800&display=swap">
<style>
  :root {
    --backdrop: #2a2a2a;
    --card: #1f1f20;
    --card-back: #1a1a1b;
    --pattern: #232324;
    --green: #1f9a45;
    --white: #f4f4f4;
    --text-soft: #e6e6e6;
    --gloss-light: #4a4a4c;
    --gloss-dark: #141415;
  }
  * { margin: 0; padding: 0; box-sizing: border-box; }
  html, body {
    width: 1200px; height: 900px; overflow: hidden;
    background: var(--backdrop);
    font-family: "Montserrat", sans-serif;
  }
  .canvas {
    position: relative; width: 1200px; height: 900px;
    display: flex; flex-direction: column; align-items: center;
    justify-content: center; gap: 40px;
  }
  .card {
    position: relative; width: 700px; height: 400px;
    border-radius: 18px; overflow: hidden;
    box-shadow: 0 10px 30px rgba(0,0,0,.45);
  }

  /* Back side */
  .card-back { background: var(--card-back); }
  .card-back .pattern-field {
    position: absolute; inset: 0;
    background: linear-gradient(135deg, var(--card-back) 0%, var(--pattern) 100%);
  }
  .card-back .brand-mark {
    position: absolute; right: 48px; bottom: 118px;
    display: flex; align-items: center; gap: 10px;
  }

  /* Shared brand wordmark */
  .brand-square { width: 14px; height: 14px; background: var(--green); }
  .brand-name {
    color: var(--white); font-weight: 800; letter-spacing: .08em;
    text-transform: uppercase; line-height: 1;
  }
  .card-back .brand-name { font-size: 17px; }

  /* Front side */
  .card-front { background: var(--card); }
  .card-front .gloss { position: absolute; inset: 0; }
  .card-front .accent-band {
    position: absolute; left: 0; right: 0; bottom: 0; height: 12px;
    background: var(--green);
  }
  .front-content { position: absolute; left: 56px; top: 56px; }
  .card-front .brand-mark { display: flex; align-items: center; gap: 14px; }
  .card-front .brand-square { width: 22px; height: 22px; }
  .card-front .brand-name { font-size: 30px; }

  .person { margin-top: 44px; }
  .person-name {
    color: var(--green); font-weight: 800; font-size: 34px;
    letter-spacing: .03em; text-transform: uppercase; line-height: 1.05;
  }
  .person-title {
    color: var(--text-soft); font-weight: 400; font-size: 20px; margin-top: 4px;
  }
  .divider { width: 22px; height: 2px; background: var(--green); margin: 18px 0 14px; }
  .contact-list { list-style: none; }
  .contact-item {
    display: flex; align-items: center; gap: 12px;
    color: var(--white); font-size: 17px; font-weight: 500; line-height: 30px;
  }
  .contact-icon { width: 16px; height: 16px; flex: none; }
</style>
</head>
<body>
<main class="canvas">

  <section class="card card-back" aria-label="Business card back">
    <div class="pattern-field" role="img" aria-label="Tonal repeating brand pattern across the card"></div>
    <div class="brand-mark">
      <span class="brand-square"></span>
      <span class="brand-name">TMW Home Crafting</span>
    </div>
  </section>

  <section class="card card-front" aria-label="Business card front">
    <svg class="gloss" viewBox="0 0 700 400" preserveAspectRatio="none" aria-hidden="true">
      <defs>
        <linearGradient id="roofGloss" x1="0" y1="1" x2="1" y2="0">
          <stop offset="0" stop-color="var(--gloss-dark)"/>
          <stop offset="0.7" stop-color="var(--gloss-light)"/>
          <stop offset="1" stop-color="#6a6a6c"/>
        </linearGradient>
      </defs>
      <polygon points="380,400 560,150 700,190 700,215 575,185 430,400" fill="url(#roofGloss)"/>
      <polygon points="430,400 575,185 700,215 700,400" fill="var(--card)"/>
    </svg>

    <div class="front-content">
      <div class="brand-mark">
        <span class="brand-square"></span>
        <span class="brand-name">TMW Home Crafting</span>
      </div>

      <div class="person">
        <h1 class="person-name">Daniel Hargrove</h1>
        <p class="person-title">CEO/Founder</p>
      </div>

      <div class="divider"></div>

      <ul class="contact-list">
        <li class="contact-item">
          <svg class="contact-icon" viewBox="0 0 24 24" aria-hidden="true"><path fill="var(--green)" d="M6.6 10.8a15.5 15.5 0 0 0 6.6 6.6l2.2-2.2c.3-.3.7-.4 1-.2 1.1.4 2.3.6 3.6.6.6 0 1 .4 1 1V20c0 .6-.4 1-1 1A17 17 0 0 1 3 4c0-.6.4-1 1-1h3.5c.6 0 1 .4 1 1 0 1.3.2 2.5.6 3.6.1.3 0 .7-.2 1z"/></svg>
          <span>555-201-7734</span>
        </li>
        <li class="contact-item">
          <svg class="contact-icon" viewBox="0 0 24 24" aria-hidden="true"><rect x="2" y="5" width="20" height="14" rx="1" fill="var(--green)"/><path d="M3 6l9 7 9-7" fill="none" stroke="var(--card)" stroke-width="1.8"/></svg>
          <span>info@tmwhomecrafting.com.au</span>
        </li>
        <li class="contact-item">
          <svg class="contact-icon" viewBox="0 0 24 24" aria-hidden="true"><g fill="none" stroke="var(--green)" stroke-width="2"><circle cx="12" cy="12" r="9"/><ellipse cx="12" cy="12" rx="4" ry="9"/><path d="M3 12h18M5 7h14M5 17h14"/></g></svg>
          <span>www.tmwhomecrafting.com.au</span>
        </li>
      </ul>
    </div>

    <div class="accent-band"></div>
  </section>

</main>
</body>
</html>
```